Business Card Design Project

After recently finishing a design project for the company logo using markbazaar, it's now time for a business card. Attached to this is the logo.

The requirements for the business card are pretty straightforward:

- A clean, uncomplicated look
- Consistent usage of fonts
- Designs for both single sided and double sided cards
- A modern layout with preferably space to refer to social media accounts and/or downloadable vcards through a qr code
- consistent application of the company colour scheme: red/white. Hex codes for exact colour can be provided

Thanks!

```html
<!DOCTYPE html>
<html lang="en">
<head>
<meta charset="utf-8">
<title>Kiln Row Staffing – Business Card</title>
<link rel="stylesheet" href="https://fonts.googleapis.com/css2?family=Open+Sans:ital,wght@0,400;0,600;0,700;1,700&display=swap">
<style>
  :root {
    --brand-red: #e31e2a;
    --band-grey: #8a8a8a;
    --ink: #231f20;
    --text-grey: #2e2e2e;
    --card-white: #ffffff;
    --backdrop: #d9d6d2;
  }
  * { box-sizing: border-box; margin: 0; padding: 0; }
  html, body {
    width: 960px;
    height: 1200px;
    overflow: hidden;
  }
  body {
    position: relative;
    background: var(--backdrop);
    font-family: "Open Sans", Arial, sans-serif;
    color: var(--text-grey);
  }
  .card {
    position: absolute;
    width: 838px;
    height: 480px;
    background: var(--card-white);
    border-radius: 30px;
    overflow: hidden;
    box-shadow: 0 6px 14px rgba(0,0,0,0.25);
  }
  .card--front { left: 60px; top: 88px; }
  .card--back  { left: 56px; top: 638px; }

  .front-header {
    position: absolute;
    left: 0; top: 0;
    width: 838px; height: 150px;
    background: linear-gradient(to bottom, var(--brand-red) 0%, var(--brand-red) 82%, var(--band-grey) 100%);
  }
  .holder {
    position: absolute;
    right: 33px; top: 38px;
    text-align: right;
    color: var(--card-white);
  }
  .holder__name {
    font-size: 30px;
    font-weight: 700;
    line-height: 38px;
  }
  .holder__role {
    font-size: 22px;
    font-weight: 400;
    line-height: 34px;
  }

  .brand {
    position: absolute;
    display: flex;
    align-items: center;
  }
  .brand__mark {
    background: var(--brand-red);
    flex: none;
  }
  .brand__name {
    color: var(--ink);
    font-weight: 600;
    white-space: nowrap;
    letter-spacing: -0.5px;
  }
  .card--front .brand { left: 44px; top: 190px; }
  .card--front .brand__mark { width: 62px; height: 62px; margin-right: 24px; }
  .card--front .brand__name { font-size: 52px; }

  .card--back .brand {
    left: 0; right: 0; top: 196px;
    justify-content: center;
  }
  .card--back .brand__mark { width: 76px; height: 76px; margin-right: 30px; }
  .card--back .brand__name { font-size: 64px; }

  .contact {
    position: absolute;
    left: 43px; top: 340px;
    list-style: none;
    font-size: 22px;
    line-height: 38px;
  }
  .contact__label {
    font-weight: 700;
    font-style: italic;
  }
  .address {
    position: absolute;
    right: 33px; top: 388px;
    font-style: normal;
    text-align: right;
    font-size: 22px;
    line-height: 32px;
  }
</style>
</head>
<body>

  <section class="card card--front" aria-label="Card front">
    <div class="front-header" role="img" aria-label="Decorative red and grey header band"></div>

    <div class="holder">
      <p class="holder__name">Your Name</p>
      <p class="holder__role">Designation</p>
    </div>

    <div class="brand">
      <span class="brand__mark"></span>
      <span class="brand__name">Kiln Row Staffing</span>
    </div>

    <ul class="contact">
      <li><span class="contact__label">t</span> : 123-123-1234</li>
      <li><span class="contact__label">e</span> : info@yourwebsite.com</li>
      <li><span class="contact__label">w</span> : www.kilnrow.com</li>
    </ul>

    <address class="address">
      1234, Street Name, City<br>
      District, Country Code.
    </address>
  </section>

  <section class="card card--back" aria-label="Card back">
    <div class="brand">
      <span class="brand__mark"></span>
      <span class="brand__name">Kiln Row Staffing</span>
    </div>
  </section>

</body>
</html>
```